Risk Management Company in need of Business Card Design

We sell risk management insurance to Lenders (Banks, Credit Unions, Real Estate Trust).

We need a very clean, professional card that will leave a great impression.

We are looking to use a blue color for our logo on the card (Preferably close to royal blue but are open to looking at navy blue or any darker blues as well).

Please see the logo attached to get an idea. We are open to writing Harbor Ledger Under the logo or next to the logo. Really whatever looks best.

Target Market(s)

Banks, Credit Unions, Real Estate Trusts

Industry/Entity Type

Insurance

Contact Information for Business Card

Name: Tom Brandish
Title: Regional Sales Director
Email: tbrandish@harborledger-example.net
C:410-555-0137
D:301-555-0182
800-555-0149 Ext.318
F:240-555-0164 (We would like to see some cards without the fax number as well to compare)

Company Name: Harbor Ledger
Website: www.harborledger-example.net

Address: 718 E. Marlow St. Suite 340, Millbrook, MD 21287 (Preferably written on the bottom of the card in small print.)

Colors
0355a3
0455a3

Requirements
Nice to have
• We would like to see a couple of where the back has the logo in reverse colors (Logo White, Background Blue)

```html
<!DOCTYPE html>
<html lang="en">
<head>
<meta charset="utf-8">
<title>Harbor Ledger – Business Cards</title>
<link rel="stylesheet" href="https://fonts.googleapis.com/css2?family=Marcellus&family=Open+Sans:wght@400;600;700&display=swap">
<style>
  :root{
    --royal:#0355a3;
    --slate:#304b58;
    --white:#ffffff;
    --stage:#e9ebee;
  }
  *{box-sizing:border-box;margin:0;padding:0}
  html,body{width:1200px;height:745px;overflow:hidden;background:var(--stage)}
  .sheet{
    width:1200px;height:745px;
    display:grid;
    grid-template-columns:540px 540px;
    grid-template-rows:308px 308px;
    gap:40px;
    padding:44px 40px;
  }
  .card{
    border-radius:22px;
    overflow:hidden;
    position:relative;
    box-shadow:0 6px 18px rgba(0,0,0,.18);
  }
  .brand{
    display:flex;flex-direction:column;align-items:center;justify-content:center;
    height:100%;
  }
  .brand-mark{width:74px;height:74px;margin-bottom:22px}
  .brand-name{
    font-family:"Marcellus",serif;
    font-size:46px;letter-spacing:1px;line-height:1;white-space:nowrap;
  }
  .brand-url{
    font-family:"Open Sans",sans-serif;font-weight:700;
    font-size:17px;letter-spacing:3px;margin-top:12px;white-space:nowrap;
  }
  /* front */
  .card-front{display:flex;background:var(--white)}
  .front-brand{width:42%;padding:10px 8px 0}
  .front-brand .brand-mark{width:54px;height:54px;margin-bottom:16px}
  .front-brand .brand-name{font-size:22px;letter-spacing:.5px;color:var(--slate)}
  .front-divider{width:10px;background:var(--white);border-left:3px solid var(--royal);border-right:2px solid var(--royal)}
  .front-contact{
    flex:1;background:var(--royal);color:var(--white);
    font-family:"Open Sans",sans-serif;padding:30px 16px 0 22px;
  }
  .contact-name{font-weight:700;font-size:18px}
  .contact-title{font-size:15px;margin-bottom:18px}
  .contact-list{list-style:none;font-size:13.5px;line-height:25px}
  .contact-list li{display:flex;align-items:center;gap:8px;white-space:nowrap}
  .contact-list svg{width:12px;height:12px;flex:none}
  .contact-ext{font-size:10px;margin-left:-3px}
  .contact-address{font-size:13.5px;line-height:18px;margin-top:10px}
  /* backs */
  .back-white{background:var(--white);color:var(--slate)}
  .back-white .brand-url{color:#222}
  .back-slate{background:var(--slate);color:var(--white)}
  .back-royal{background:var(--royal);color:var(--white)}
  .back-royal .brand-url{font-family:"Marcellus",serif;font-weight:400;letter-spacing:4px}
</style>
</head>
<body>
<main class="sheet">

  <section class="card card-front">
    <div class="brand front-brand">
      <svg class="brand-mark" viewBox="0 0 10 10"><rect width="10" height="10" fill="var(--slate)"/></svg>
      <div class="brand-name">HARBOR LEDGER</div>
    </div>
    <div class="front-divider"></div>
    <div class="front-contact">
      <div class="contact-name">Tom Brandish</div>
      <div class="contact-title">Regional Sales Director</div>
      <ul class="contact-list">
        <li><svg viewBox="0 0 12 12"><path d="M2 1h3l1 3-2 1a7 7 0 0 0 3 3l1-2 3 1v3c-6 0-10-4-10-9z" fill="#fff"/></svg>301-555-0182</li>
        <li><svg viewBox="0 0 12 12"><path d="M2 1h3l1 3-2 1a7 7 0 0 0 3 3l1-2 3 1v3c-6 0-10-4-10-9z" fill="#fff"/></svg>800-555-0149 <span class="contact-ext">Ext.318</span></li>
        <li><svg viewBox="0 0 12 12"><rect x="3" y="1" width="6" height="4" fill="#fff"/><rect x="1" y="5" width="10" height="5" rx="1" fill="#fff"/></svg>240-555-0164</li>
        <li><svg viewBox="0 0 12 12"><rect x="1" y="3" width="10" height="7" fill="#fff"/><path d="M1 3l5 4 5-4" stroke="var(--royal)" fill="none"/></svg>tbrandish@harborledger-example.net</li>
        <li><svg viewBox="0 0 12 12"><circle cx="6" cy="6" r="5" fill="none" stroke="#fff" stroke-width="1.4"/><path d="M1 6h10M6 1v10" stroke="#fff"/></svg>www.harborledger-example.net</li>
      </ul>
      <div class="contact-address">718 E. Marlow St., Suite 340<br>Millbrook MD 21287</div>
    </div>
  </section>

  <section class="card back-slate">
    <div class="brand">
      <svg class="brand-mark" viewBox="0 0 10 10"><rect width="10" height="10" fill="var(--white)"/></svg>
      <div class="brand-name">HARBOR LEDGER</div>
      <div class="brand-url">www.harborledger-example.net</div>
    </div>
  </section>

  <section class="card back-white">
    <div class="brand">
      <svg class="brand-mark" viewBox="0 0 10 10"><rect width="10" height="10" fill="var(--slate)"/></svg>
      <div class="brand-name">HARBOR LEDGER</div>
      <div class="brand-url">www.harborledger-example.net</div>
    </div>
  </section>

  <section class="card back-royal">
    <div class="brand">
      <svg class="brand-mark" viewBox="0 0 10 10"><rect width="10" height="10" fill="var(--white)"/></svg>
      <div class="brand-name">HARBOR LEDGER</div>
      <div class="brand-url">WWW.HARBORLEDGER-EXAMPLE.NET</div>
    </div>
  </section>

</main>
</body>
</html>
```